High-end construction company needs a business card design

We need a modern looking business card that draws people in, is memorable and looks so good people will want to sick it on their fridges.
On the first side what is needed are:
Logo
My name - Tomasz Brelwik
Title - Managing Director
Website - www.varkelt.co.uk
Email - tomasz@varkelt.co.uk
Telephone - 020 5194 6281
Mobile - 07845139072
On the back side was is needed is a list of all the services we provide:
-Kitchen Renovations
-Bathroom Renovations
-House Renovations
-Garage Conversions
-Extensions
-Loft Conversions
-Conservatories
-Carpentry
-Tiling
-Electrical
-Plumbing & Heating
-Bricklaying
-Landscaping
-Decorating
-Plastering
We would like the colours to be the same shades as on the logo with grey or black for the words.
Target Market(s)
Anyone who needs building work done
Contact Information for Business Card
This business card is for a construction company which strives to deliver excellent service and quality.
The look and feel of the card should represent this.
Requirements
Must have
- On the first side what is needed are:
Logo
My name - Tomasz Brelwik
Title - Managing Director
Website - www.varkelt.co.uk
Email - tomasz@varkelt.co.uk
Telephone - 020 5194 6281
Mobile - 07845139072
Nice to have
- Cool looking features

```html
<!DOCTYPE html>
<html lang="en">
<head>
<meta charset="utf-8">
<title>Varkelt Construction Ltd – Business Card</title>
<link href="https://fonts.googleapis.com/css2?family=Montserrat:wght@500;700;800&family=Quicksand:wght@400;500&display=swap" rel="stylesheet">
<style>
  :root{
    --green:#4fa93a;
    --green-light:#6fbe45;
    --green-dark:#3a8a33;
    --grey:#6d6e6d;
    --white:#ffffff;
    --ink:#4a4a4a;
    --bg:#e6e7e6;
  }
  *{margin:0;padding:0;box-sizing:border-box}
  html,body{width:1200px;height:965px;overflow:hidden;background:var(--bg)}
  .stage{position:relative;width:1200px;height:965px}
  .card{position:absolute;left:230px;width:740px;height:423px;overflow:hidden;box-shadow:0 6px 18px rgba(0,0,0,.18)}
  .card--services{top:40px;background:radial-gradient(circle at 60% 20%,var(--green-light),var(--green-dark) 85%)}
  .card--contact{top:500px;background:var(--white)}

  .wordmark{font-family:"Montserrat",sans-serif;font-weight:800;text-transform:uppercase;line-height:1;letter-spacing:.04em}
  .card--services .wordmark{position:absolute;top:52px;left:0;width:100%;text-align:center;color:var(--white)}
  .wordmark__name{display:block;font-size:58px}
  .wordmark__sub{display:block;font-size:17px;letter-spacing:.2em;margin-top:8px}

  .services{position:absolute;top:190px;left:0;width:100%;list-style:none}
  .services__band{background:var(--white);height:36px;margin:0 24px 10px 60px;display:flex;align-items:center;justify-content:center;gap:10px;
    font-family:"Quicksand",sans-serif;font-weight:500;font-size:16px;color:var(--ink);text-transform:uppercase;letter-spacing:.01em}
  .services__band:nth-child(2){margin-left:40px}
  .services__band:nth-child(3){margin-left:80px}
  .services__band:nth-child(4){margin-left:100px}
  .dot{width:11px;height:11px;border-radius:50%;background:var(--green);flex:none}

  .contact-art{position:absolute;inset:0}
  .card--contact .wordmark{position:absolute;top:92px;left:70px;color:var(--green)}
  .card--contact .wordmark__name{font-size:54px}
  .card--contact .wordmark__sub{font-size:15px}

  .person{position:absolute;left:44px;bottom:40px;color:var(--white)}
  .person__name{font-family:"Montserrat",sans-serif;font-weight:700;font-size:30px;text-transform:uppercase;letter-spacing:.03em}
  .person__title{font-family:"Quicksand",sans-serif;font-weight:500;font-size:19px;margin-top:2px}

  .details{position:absolute;right:30px;top:175px;list-style:none;color:var(--white);font-family:"Quicksand",sans-serif;font-weight:500;font-size:17px;text-align:right}
  .details li{display:flex;align-items:center;justify-content:flex-end;gap:10px;height:27px}
  .details svg{width:16px;height:16px;flex:none}
</style>
</head>
<body>
<main class="stage">

  <section class="card card--services" aria-label="Services side">
    <div class="wordmark">
      <span class="wordmark__name">Varkelt</span>
      <span class="wordmark__sub">Construction Ltd</span>
    </div>
    <ul class="services">
      <li class="services__band">Kitchen Renovations<span class="dot"></span>Bathroom Renovations<span class="dot"></span>House Renovations</li>
      <li class="services__band">Garage Conversions<span class="dot"></span>Extensions<span class="dot"></span>Loft Conversions<span class="dot"></span>Conservatories</li>
      <li class="services__band">Carpentry<span class="dot"></span>Tiling<span class="dot"></span>Electrical<span class="dot"></span>Plumbing &amp; Heating</li>
      <li class="services__band">Bricklaying<span class="dot"></span>Landscaping<span class="dot"></span>Decorating<span class="dot"></span>Plastering</li>
    </ul>
  </section>

  <section class="card card--contact" aria-label="Contact side">
    <svg class="contact-art" viewBox="0 0 740 423" preserveAspectRatio="none" aria-hidden="true">
      <defs>
        <radialGradient id="greenGlow" cx="70%" cy="55%" r="70%">
          <stop offset="0" stop-color="#6fbe45"/>
          <stop offset="1" stop-color="#3a8a33"/>
        </radialGradient>
      </defs>
      <path d="M0,225 C280,205 520,130 740,58 L740,423 L0,423Z" fill="#6d6e6d"/>
      <path d="M0,320 C280,262 520,172 740,98 L740,423 L0,423Z" fill="url(#greenGlow)"/>
      <path d="M0,320 C280,262 520,172 740,98" fill="none" stroke="#fff" stroke-width="7"/>
    </svg>

    <div class="wordmark">
      <span class="wordmark__name">Varkelt</span>
      <span class="wordmark__sub">Construction Ltd</span>
    </div>

    <div class="person">
      <p class="person__name">Tomasz Brelwik</p>
      <p class="person__title">Managing Director</p>
    </div>

    <ul class="details">
      <li>078 4513 9072
        <svg viewBox="0 0 16 16"><rect x="4" y="1" width="8" height="14" rx="1.5" fill="none" stroke="#fff" stroke-width="1.3"/><circle cx="8" cy="12.5" r=".9" fill="#fff"/></svg></li>
      <li>020 5194 6281
        <svg viewBox="0 0 16 16"><path d="M3 2l3 1 1 3-2 1.5a8 8 0 0 0 3.5 3.5L10 9l3 1 1 3-2 1.5C6 14 2 10 1.5 4z" fill="none" stroke="#fff" stroke-width="1.2" stroke-linejoin="round"/></svg></li>
      <li>tomasz@varkelt.co.uk
        <svg viewBox="0 0 16 16"><rect x="1" y="3" width="14" height="10" fill="none" stroke="#fff" stroke-width="1.2"/><path d="M1 3l7 6 7-6" fill="none" stroke="#fff" stroke-width="1.2"/></svg></li>
      <li>www.varkelt.co.uk
        <svg viewBox="0 0 16 16"><circle cx="8" cy="8" r="6.5" fill="none" stroke="#fff" stroke-width="1.2"/><ellipse cx="8" cy="8" rx="3" ry="6.5" fill="none" stroke="#fff" stroke-width="1"/><path d="M1.5 8h13" stroke="#fff" stroke-width="1"/></svg></li>
    </ul>
  </section>

</main>
</body>
</html>
```